Maple Beacon Website

We are starting a marketing company and to do that we need a website! We want a website that will inspire and persuade to bring out the awesomeness in our clients.
What we want to see:
- Inspirational and persuasive imagery that relate to Branding.
- No cliche images eg. business man, suits and hand shakes
- We want to transform and educate our clients.
- We want to show them the path and would like our website to really act as a guide that guides them step by step through our process.
- We want the portray that we are an investment but not have a pretentious way to it. We put our heart into every project and that is how we treat our clients.
-When you submit your design please include what platform you have created for. Preference would be Wordpress or Joobla.

We have included the psd file for the wire frame, logo files, font files, site map and a link to a video we create to give you more information on what we would like to see. http://clipvault.example/t/qk82LmZpr

Feel free to make small modification to the logos if you think it will improve it. Your creativity and advice is most welcome.
Updates

One thing we forgot. We would like to have our contact information near the top of the website as well as at the bottom.  Here is out contact info:

Email: info@maplebeacon.example
Phone: 587-555-0142

Project Deadline Extended
Reason: As we are new with the platform and that we want to optimize our results, we decided to extend the deadline by 15 days. Thanks!

Target Market(s)

28-60, Male and Female, Oil field, Local Businesses, Dentists, Chiropractors, Hair salon, Construction/Renovation, Events etc

Industry/Entity Type

Investment

Requirements
Must have
• - 4 Inspirational and persuasive Imagery for the top portion of the website
- Must have a feel as if your not on a website an example of this is linked below.
http://www.artbidhub.example/design/402957/web-design-by-lena-torvik
Nice to have
• - Creative advice from you.
- Creative buttons for Get Free Quote and Subscribe buttons. Something out of the box that draws peoples attention. eg. a 'B' button. Just and example but still something related to branding.
Should not have
• No Cliches

```html
<!DOCTYPE html>
<html lang="en">
<head>
<meta charset="utf-8">
<title>Maple Beacon</title>
<link href="https://fonts.googleapis.com/css2?family=Alfa+Slab+One&family=Arimo:wght@400;700&family=Fredoka:wght@600&family=Lora:ital,wght@0,700;1,700&family=Open+Sans:ital,wght@0,400;0,600;1,400&family=PT+Sans+Narrow&display=swap" rel="stylesheet">
<style>
:root{
  --green:#5b9a1e;
  --green-bright:#8bd12c;
  --green-deep:#3f7f16;
  --grey-text:#8a8a8a;
  --grey-dark:#4a4a4a;
  --grey-mid:#6b6b6b;
  --grey-light:#c4c4c4;
  --white:#ffffff;
}
*{margin:0;padding:0;box-sizing:border-box}
html,body{width:1200px;height:953px;overflow:hidden}
body{position:relative;background:linear-gradient(#f7f7f7 0,#ffffff 420px,#ffffff 800px,#f2f2f2 100%);font-family:"Open Sans",sans-serif;color:var(--grey-dark)}
.abs{position:absolute;white-space:nowrap}

.brand-box{left:35px;top:0;width:283px;height:141px;background:var(--white)}
.brand-name{left:56px;top:42px;display:flex;align-items:center;gap:10px;font-family:"Open Sans",sans-serif;font-weight:600;font-size:31px;color:var(--grey-mid);letter-spacing:-.3px}
.brand-dot{width:22px;height:22px;border-radius:50%;background:var(--green-bright)}
.tagline{left:35px;top:114px;width:283px;text-align:center;font-style:italic;font-size:15px;color:var(--grey-dark)}

.side-nav{left:35px;top:141px;width:283px;height:233px;background:linear-gradient(#ffffff,#e4e4e4)}
.side-nav ul{list-style:none;position:absolute;left:24px;top:28px}
.side-nav li{font-size:20px;line-height:28.5px;color:#222;letter-spacing:-.3px}
.connect-title{position:absolute;left:0;width:283px;top:192px;text-align:center;font-family:"Fredoka",sans-serif;font-weight:600;font-size:25px;color:var(--grey-dark)}

.contact-top{top:24px;display:flex;align-items:center;gap:9px;font-family:"Arimo",sans-serif;font-weight:700;font-size:15px;color:var(--grey-dark)}
.contact-top .label{color:var(--green)}
.icon-disc{flex:none;width:38px;height:38px;border-radius:50%;background:radial-gradient(circle at 40% 35%,#fafafa,#c9c9c9);display:flex;align-items:center;justify-content:center;font-size:22px;color:var(--grey-dark)}
.top-rule{left:394px;top:66px;width:771px;height:1px;background:#e2e2e2}

.steps{left:398px;top:77px;display:flex;font-family:"PT Sans Narrow",sans-serif;font-size:21px;color:#a9a9a9}
.step{display:flex;align-items:center;gap:8px;margin-right:22px}
.step i{width:17px;height:17px;border-radius:50%;background:var(--grey-light);display:block}
.step.is-active{color:var(--green)}
.step.is-active i{background:var(--green-bright)}

.hero-art{left:412px;top:141px;width:458px;height:235px;background:radial-gradient(ellipse at 50% 45%,#d8e9d0 0,#e8eef4 45%,rgba(255,255,255,0) 75%)}

.news-band{left:35px;top:378px;width:1130px;height:53px;background:linear-gradient(#9ee03a,#6fb422 60%,#5a9a1a);box-shadow:0 2px 3px rgba(0,0,0,.12)}
.social{position:absolute;top:8px;width:37px;height:37px;border-radius:5px;background:linear-gradient(#fdfdfd,#cfcfcf);box-shadow:0 1px 2px rgba(0,0,0,.3)}
.news-text{position:absolute;left:274px;top:12px;font-family:"Lora",serif;font-style:italic;font-weight:700;font-size:21px;color:var(--white);white-space:nowrap}
.btn-subscribe{position:absolute;left:760px;top:4px;width:157px;height:43px;border-radius:9px;background:linear-gradient(#ffffff,#e3e3e3);display:flex;align-items:center;justify-content:center;font-family:"Fredoka",sans-serif;font-weight:600;font-size:18px;color:var(--green-deep);white-space:nowrap}

.welcome{left:0;width:1180px;top:466px;text-align:center;font-family:"Alfa Slab One",serif;font-weight:400;font-size:26px;color:#5e5e5e;letter-spacing:.3px}
.welcome span{color:var(--green)}
.intro{left:284px;width:660px;white-space:normal;font-family:"Arimo",sans-serif;font-weight:700;font-size:13px;line-height:21.2px;color:var(--grey-text)}
.intro p+p{margin-top:21px}

.btn-quote{left:739px;top:738px;width:202px;height:43px;border-radius:7px;background:linear-gradient(#7cc433,#3f8a17);box-shadow:0 2px 3px rgba(0,0,0,.3);display:flex;align-items:center;justify-content:center;gap:8px;font-family:"Lora",serif;font-weight:700;font-size:22px;color:var(--white);letter-spacing:.5px}

.footer-rule{left:0;top:809px;width:1200px;height:1px;background:#ececec}
.footer-nav{left:0;width:1200px;top:857px;display:flex;justify-content:center;font-family:"Arimo",sans-serif;font-size:14px;color:var(--grey-dark)}
.footer-nav span.sep{margin:0 30px}
.footer-contact{left:0;width:1200px;top:900px;display:flex;justify-content:center;gap:20px;font-family:"Arimo",sans-serif;font-size:14px;color:var(--green)}
.footer-contact .copy{color:var(--grey-dark)}
</style>
</head>
<body>

<div class="abs brand-box"></div>
<div class="abs brand-name"><span class="brand-dot"></span>Maple Beacon</div>
<div class="abs tagline">Because You´re Awesome!</div>

<nav class="abs side-nav">
  <ul>
    <li>STRATEGY</li>
    <li>PORTFOLIO</li>
    <li>ABOUT US</li>
    <li>CONTACT US</li>
    <li>BLOG</li>
  </ul>
  <div class="connect-title">Connect with us!</div>
</nav>

<div class="abs contact-top" style="left:505px">
  <div class="icon-disc">@</div>
  <span><span class="label">Email:</span> info@maplebeacon.example</span>
</div>
<div class="abs contact-top" style="left:862px">
  <div class="icon-disc">
    <svg width="20" height="20" viewBox="0 0 24 24"><path d="M6.6 10.8c1.4 2.8 3.8 5.1 6.6 6.6l2.2-2.2c.3-.3.7-.4 1-.2 1.1.4 2.3.6 3.6.6.6 0 1 .4 1 1V20c0 .6-.4 1-1 1C10.6 21 3 13.4 3 4c0-.6.4-1 1-1h3.5c.6 0 1 .4 1 1 0 1.3.2 2.5.6 3.6.1.3 0 .7-.2 1z" fill="#4a4a4a"/></svg>
  </div>
  <span><span class="label">Phone:</span> 587-555-0142</span>
</div>
<div class="abs top-rule"></div>

<div class="abs steps">
  <div class="step is-active"><i></i>Maple Beacon</div>
  <div class="step"><i></i>Be Found</div>
  <div class="step"><i></i>Connect</div>
  <div class="step"><i></i>Get Growing</div>
</div>

<div class="abs hero-art" role="img" aria-label="Illustration of figures holding coloured puzzle pieces spelling BRAND"></div>

<div class="abs news-band">
  <div class="social" style="left:50px"></div>
  <div class="social" style="left:103px"></div>
  <div class="social" style="left:156px"></div>
  <div class="news-text">Get Tips and Tricks! Subscribe to our Newsletter.</div>
  <div class="btn-subscribe">SUBSCRIBE NOW</div>
</div>

<h1 class="abs welcome"><span>WELCOME TO</span> MAPLE BEACON</h1>

<div class="abs intro" style="top:533px">
  <p>This is just a bunch of words put toghether to make it look like&nbsp; paragraph. It is purly for show and filler so that we can have a general idea of what it will ook like when we put in the proper pagaraphs thatmake up our mission statment. I think this font size looks pretty good but maybe be a tad bit smaler.&nbsp; would like to see the welcome a little more dramatic looking. I think that</p>
  <p>is all I need to write here for now. This is just a bunch of words put toghether to make it look like&nbsp; paragraph. It is purly for show and filler so that we can have a general idea of what it will ook like when we put in the proper pagaraphs thatmake up our mission statment. I think this font size looks pretty good but maybe be a tad bit smaler.&nbsp; would like to see the welcome a little more dramatic looking. I think</p>
</div>

<div class="abs btn-quote">FREE QUOTE
  <svg width="12" height="16" viewBox="0 0 12 16"><path d="M0 0L12 8L0 16Z" fill="#ffffff"/></svg>
</div>

<div class="abs footer-rule"></div>
<div class="abs footer-nav">
  <span>Site Map</span><span class="sep">/</span>
  <span>Strategy</span><span class="sep">/</span>
  <span>Portfolio</span><span class="sep">/</span>
  <span>About Us</span><span class="sep">/</span>
  <span>Contact Us</span><span class="sep">/</span>
  <span>Blog</span>
</div>
<div class="abs footer-contact">
  <span>Contact info&nbsp; : &nbsp;Email: info@maplebeacon.example</span>
  <span>Phone: 587-555-0142</span>
  <span class="copy">©MAPLE BEACON INC. 2013</span>
</div>

</body>
</html>
```